Stylish new business card needed!

Hello everyone! I am in need of a new business card design for an alarm company here in Hurricane WV. I have all fonts, color codes and logos provided for you use! We are a young company and like the style of a clean sleek looking business card. Would like it double sided, one side holding the logo and the other with your design!
Target Market(s)
The people that are looking for the newest tech for home automation and security
Industry/Entity Type
Alarm services; Home automation
Contact Information for Business Card
Name of person; position (Sales; Installer); Phone Number (555.418.7260); Employee cell Number; Website (www.GuardedByVelk.example); Employee Email; Double sided
Look and feel
Each slider illustrates characteristics of the customer's brand and the style your logo design should communicate.

```html
<!DOCTYPE html>
<html lang="en">
<head>
<meta charset="utf-8">
<title>Guarded By Velk – Business Card</title>
<link rel="stylesheet" href="https://fonts.googleapis.com/css2?family=Archivo+Black&family=Lato:wght@400;700;900&display=swap">
<style>
  :root {
    --backdrop: #3b3b3d;
    --card: #27282a;
    --orange: #ff8c42;
    --grey: #9a9a9a;
    --white: #ffffff;
  }
  * { margin: 0; padding: 0; box-sizing: border-box; }
  html, body { width: 1200px; height: 937px; overflow: hidden; }
  body {
    background: var(--backdrop);
    position: relative;
    font-family: "Lato", sans-serif;
  }
  .card {
    position: absolute;
    left: 290px;
    width: 620px;
    height: 354px;
    background: var(--card);
    overflow: hidden;
  }
  .card--front { top: 92px; }
  .card--back { top: 492px; }
  .card__stripe {
    position: absolute;
    left: 0; right: 0; bottom: 0;
    height: 9px;
    background: var(--orange);
  }
  .brand {
    position: absolute;
    text-align: center;
    color: var(--orange);
  }
  .brand__name {
    font-family: "Archivo Black", sans-serif;
    color: var(--orange);
    line-height: 1;
    letter-spacing: 1px;
  }
  .brand__tagline {
    font-family: "Archivo Black", sans-serif;
    letter-spacing: 1.5px;
    margin-top: 10px;
  }
  .card--front .brand {
    left: 0; right: 0; top: 128px;
  }
  .card--front .brand__name { font-size: 48px; }
  .card--front .brand__tagline { font-size: 13px; }

  .card--back .brand {
    left: 40px; width: 290px; top: 140px;
  }
  .card--back .brand__name { font-size: 30px; }
  .card--back .brand__tagline { font-size: 9px; margin-top: 8px; }

  .divider {
    position: absolute;
    left: 352px; top: 96px;
    width: 1.5px; height: 150px;
    background: var(--orange);
  }
  .contact {
    position: absolute;
    left: 380px; top: 92px;
    color: var(--white);
  }
  .contact__name {
    font-family: "Archivo Black", sans-serif;
    color: var(--orange);
    font-size: 24px;
    line-height: 1;
    letter-spacing: 0.5px;
  }
  .contact__role {
    font-size: 14px;
    margin: 4px 0 0 16px;
  }
  .contact__list {
    list-style: none;
    margin: 14px 0 0 28px;
  }
  .contact__item {
    display: flex;
    align-items: center;
    gap: 7px;
    font-size: 14px;
    line-height: 22px;
  }
  .contact__icon { width: 12px; height: 12px; flex: none; }
</style>
</head>
<body>

<section class="card card--front" aria-label="Card front">
  <div class="brand">
    <div class="brand__name">GUARDED BY VELK</div>
    <div class="brand__tagline">AUTOMATION AND SECURITY SERVICES</div>
  </div>
  <div class="card__stripe"></div>
</section>

<section class="card card--back" aria-label="Card back">
  <div class="brand">
    <div class="brand__name">GUARDED BY VELK</div>
    <div class="brand__tagline">AUTOMATION AND SECURITY SERVICES</div>
  </div>
  <div class="divider"></div>
  <div class="contact">
    <div class="contact__name">DALE HARTWELL</div>
    <div class="contact__role">Manager</div>
    <ul class="contact__list">
      <li class="contact__item">
        <svg class="contact__icon" viewBox="0 0 12 12" aria-hidden="true"><rect x="3" y="0.5" width="6" height="11" rx="1" fill="none" stroke="#ff8c42" stroke-width="1.2"/><circle cx="6" cy="9.6" r="0.7" fill="#ff8c42"/></svg>
        000-000-0000
      </li>
      <li class="contact__item">
        <svg class="contact__icon" viewBox="0 0 12 12" aria-hidden="true"><path d="M2.5 1 L4.5 1 L5.3 3.6 L4 4.6 Q5 7 7.4 8 L8.4 6.7 L11 7.5 L11 9.5 Q10.5 11 9 11 Q1 10 1 2.5 Q1 1 2.5 1Z" fill="#ff8c42"/></svg>
        555.418.7260
      </li>
      <li class="contact__item">
        <svg class="contact__icon" viewBox="0 0 12 12" aria-hidden="true"><rect x="0.5" y="2.5" width="11" height="7.5" fill="#ff8c42"/><path d="M0.5 2.5 L6 7 L11.5 2.5" fill="none" stroke="#27282a" stroke-width="1.2"/></svg>
        mail@GuardedByVelk.example
      </li>
      <li class="contact__item">
        <svg class="contact__icon" viewBox="0 0 12 12" aria-hidden="true"><circle cx="6" cy="6" r="5.3" fill="#ff8c42"/><ellipse cx="6" cy="6" rx="2.2" ry="5.3" fill="none" stroke="#27282a" stroke-width="0.9"/><path d="M0.8 6 H11.2" stroke="#27282a" stroke-width="0.9"/></svg>
        www.GuardedByVelk.example
      </li>
    </ul>
  </div>
  <div class="card__stripe"></div>
</section>

</body>
</html>
```